Letter and Envelope Design For Harborline Realty

Please design a letter and an envelope incorporating our logo (See Attached). We are also launched a business card contest. Since we want them to match, please feel free to submit a design for both the business card and also the letter design and envelope.

Requirements
Must have
• The envelope, the letter and the business cards must match somehow connecting the designs. We want them to have something that holds them together besides the logo.

```html
<!DOCTYPE html>
<html lang="en">
<head>
<meta charset="utf-8">
<title>Harborline Realty – Letterhead and Envelope</title>
<link href="https://fonts.googleapis.com/css2?family=Montserrat:wght@500&family=PT+Sans:wght@400;700&family=Arimo:wght@700&display=swap" rel="stylesheet">
<style>
  :root{
    --bg:#e6e7e8;
    --paper:#f8f8f8;
    --navy:#0a1a8c;
    --blue:#1f4fa8;
    --slate:#58595b;
    --ink:#3d3d3d;
    --heading:#2a2a2a;
    --sig:#cfd0d2;
    --white:#ffffff;
  }
  *{box-sizing:border-box;margin:0;padding:0}
  html,body{width:1200px;height:825px;overflow:hidden;background:var(--bg)}
  .canvas{position:relative;width:1200px;height:825px}

  .letter{position:absolute;left:80px;top:86px;width:462px;height:652px;background:var(--paper);overflow:hidden}
  .brand{position:absolute;display:flex;flex-direction:column;align-items:center}
  .brand-dot{width:46px;height:46px;border:2.5px solid var(--navy);border-radius:50%}
  .brand-name{margin-top:6px;font-family:"Montserrat",sans-serif;font-weight:500;color:var(--navy);font-size:11.5px;letter-spacing:1.6px;text-align:center;line-height:1.25}
  .letter .brand{left:33px;top:31px;width:118px}

  .salutation{position:absolute;left:35px;top:134px;font-family:"Arimo",sans-serif;font-weight:700;font-size:10.5px;color:var(--heading)}
  .body-copy{position:absolute;left:35px;right:35px;top:159px;font-family:"PT Sans",sans-serif;font-size:9.4px;line-height:12px;color:var(--ink);text-align:justify}
  .body-copy p{margin-bottom:12px}
  .signature{position:absolute;left:40px;top:430px;width:76px;height:36px;background:var(--sig);border-radius:3px}

  .footer-band{position:absolute;left:0;right:0;bottom:0;height:58px;background:linear-gradient(180deg,var(--blue) 0%,var(--navy) 45%,var(--navy) 100%)}
  .contact{position:absolute;font-family:"PT Sans",sans-serif;color:var(--white);font-size:7.2px;line-height:11px}
  .contact strong{font-weight:700}
  .contact .row{display:flex;gap:6px;align-items:center}
  .contact svg{width:6px;height:6px;vertical-align:middle;margin-right:2px}
  .letter .contact{left:35px;top:613px}

  .envelope{position:absolute;left:589px;top:441px;width:531px;height:297px}
  .flap{position:absolute;left:0;top:0;display:block}
  .envelope-face{position:absolute;left:0;top:67px;width:531px;height:230px;background:var(--paper);overflow:hidden}
  .envelope .brand{left:26px;top:15px;width:118px}
  .envelope .contact{left:46px;top:189px}
</style>
</head>
<body>
<main class="canvas">

  <section class="letter">
    <div class="brand">
      <div class="brand-dot"></div>
      <div class="brand-name">HARBORLINE<br>REALTY</div>
    </div>

    <h1 class="salutation">Dear Mr. Avery,</h1>
    <div class="body-copy">
      <p>Lorem Ipsum is simply dummy text of the printing and typesetting industry. Lorem Ipsum has been the industry's standard dummy text ever since the 1500s, when an unknown printer took a galley of type and scrambled it to make a type specimen book. It has survived not only five centuries, but also the leap into electronic typesetting, remaining essentially unchanged.</p>
      <p>The standard chunk of Lorem Ipsum used since the 1500s is reproduced below for those interested. Sections 1.10.32 and 1.10.33 from "de Finibus Bonorum et Malorum" by Aurelian are also reproduced in their exact original form, accompanied by English versions from the 1914 translation by H. Marlow</p>
      <p>Lorem Ipsum is simply dummy text of the printing and typesetting industry. Lorem Ipsum has been the industry's standard dummy text ever since the 1500s, when an unknown printer took a galley of type and scrambled it to make a type specimen book. It has survived not only five centuries, but also the leap into electronic typesetting, remaining essentially unchanged. It was popularised in the</p>
      <p>The standard chunk of Lorem Ipsum used since the 1500s is reproduced below for those interested. Sections 1.10.32 and 1.10.33 from "de Finibus Bonorum et Malorum" by Aurelian are also reproduced in their exact original form, accompanied by English versions from the 1914 translation by H. Marlow</p>
    </div>
    <div class="signature" role="img" aria-label="Handwritten signature of the sender"></div>

    <div class="footer-band" role="img" aria-label="Decorative footer band in blue and navy"></div>
    <div class="contact">
      <strong>Harborline Realty</strong><br>
      Po. box 201, Street Name, City Name, Zip Code - 00000
      <div class="row">
        <span><svg viewBox="0 0 10 10"><path d="M2 0h2l1 3-1.5 1a6 6 0 0 0 2.5 2.5L7 5l3 1v2q0 2-2 2A9 9 0 0 1 0 2q0-2 2-2z" fill="currentColor"/></svg>555-014-2290</span>
        <span><svg viewBox="0 0 10 10"><path d="M0 2h10v6H0z" fill="currentColor"/><path d="M0 2l5 3.5L10 2" stroke="var(--navy)" fill="none"/></svg>info@harborlinerealty.com</span>
        <span><svg viewBox="0 0 10 10"><circle cx="5" cy="5" r="4.5" fill="currentColor"/></svg>www.harborlinerealty.com</span>
      </div>
    </div>
  </section>

  <section class="envelope">
    <svg class="flap" width="531" height="67" viewBox="0 0 531 67" aria-hidden="true">
      <path d="M0 67 C4 44 14 34 48 29 L255 2 Q265 0 278 1 L500 27 Q527 31 531 56 L531 67 Z" fill="var(--slate)"/>
    </svg>
    <div class="envelope-face">
      <div class="brand">
        <div class="brand-dot"></div>
        <div class="brand-name">HARBORLINE<br>REALTY</div>
      </div>
      <div class="footer-band" role="img" aria-label="Decorative footer band in blue and navy"></div>
      <div class="contact">
        <strong>Harborline Realty</strong><br>
        Po. box 201, Street Name, City Name, Zip Code - 00000
        <div class="row">
          <span><svg viewBox="0 0 10 10"><path d="M2 0h2l1 3-1.5 1a6 6 0 0 0 2.5 2.5L7 5l3 1v2q0 2-2 2A9 9 0 0 1 0 2q0-2 2-2z" fill="currentColor"/></svg>555-014-2290</span>
          <span><svg viewBox="0 0 10 10"><path d="M0 2h10v6H0z" fill="currentColor"/><path d="M0 2l5 3.5L10 2" stroke="var(--navy)" fill="none"/></svg>info@harborlinerealty.com</span>
          <span><svg viewBox="0 0 10 10"><circle cx="5" cy="5" r="4.5" fill="currentColor"/></svg>www.harborlinerealty.com</span>
        </div>
      </div>
    </div>
  </section>

</main>
</body>
</html>
```